Restyle Company web site and logo

we need a wordpress design beacause after few year we need to refresh our company web site(www.velotrastudio.example) & logo. We are a small company called VR Advisory focused on business intellegence, data quality, data integration, etc and based on Legnago (small town near to Verona (italy)).
During the 2014 we add to our skill develop project for MDM and Procurement.
We are Young (avg 30 years old). We want to change our logo and color templete to communicate to all cumstomer professional skill, precision and passion.

--- UPDATE --
The new site can be complitile different from the actual website.
The new Logo is now available.
Updates

Target Market(s)

B2B, mid size market, professional account

Industry/Entity Type

It Company

Font styles to use
Sans Serif

Colors
acd037
3277b5

Requirements
Must have
• Simple and clean/clear image colur. Professional site. it need to rapresent trust site.
• Must be responsive desk/mobile.
Nice to have
• different color area for different kind off business line.
• slider image.
Should not have
• classical image

```html
<!DOCTYPE html>
<html lang="en">
<head>
<meta charset="utf-8">
<title>VR Advisory</title>
<link rel="stylesheet" href="https://fonts.googleapis.com/css2?family=Arimo:ital,wght@0,400;0,700;1,400&family=Open+Sans:wdth,wght@75,300&display=swap">
<style>
:root{
  --green:#8dbd0f;
  --green-light:#a6d21d;
  --blue:#0b6aa2;
  --blue-dark:#07507d;
  --ink:#222;
  --muted:#555;
  --link:#1b5e9a;
  --line:#d9d9d9;
  --strip:#e7e7e7;
  --page:#f1f1f1;
}
*{margin:0;padding:0;box-sizing:border-box}
html,body{width:821px;height:1200px;overflow:hidden}
body{position:relative;background:var(--page);font-family:"Arimo",Arial,sans-serif;color:var(--ink)}
.abs{position:absolute}
.cond{font-family:"Open Sans",sans-serif;font-weight:300;font-stretch:75%}
.header{left:0;top:0;width:821px;height:98px;background:linear-gradient(#f4f4f4,#fff)}
.brand{left:78px;top:26px;display:flex;align-items:center;gap:8px;font-size:15px;font-weight:700;color:var(--blue)}
.brand-dot{width:26px;height:26px;border-radius:50%;background:var(--green)}
.connect{right:69px;top:12px;font-size:11px;color:#333;display:flex;align-items:center;gap:5px}
.connect i{display:inline-block;width:14px;height:14px;background:var(--blue);border-radius:2px}
.callline{right:69px;top:37px;font-size:11px;color:#333}
.callline span{color:var(--blue)}
.nav{left:253px;top:60px;width:500px;height:30px;background:linear-gradient(var(--green-light),var(--green));display:flex}
.nav a{flex:1;color:#111;font-size:12px;text-decoration:none;display:flex;align-items:center;justify-content:center;border-right:1px solid #7fae0b}
.nav a:last-child{border-right:0}
.rule{left:0;top:98px;width:821px;height:6px;background:#d6d6d6}
.hero{left:0;top:104px;width:821px;height:256px;background:var(--blue)}
.hero-photo{left:440px;top:104px;width:250px;height:256px;background:radial-gradient(ellipse at 50% 45%,#7fc4ec 0%,#2a84bd 45%,#0b6aa2 80%)}
.hero-title{left:79px;top:158px;font-size:34px;font-weight:400;color:#fff;letter-spacing:.5px}
.hero-sub{left:77px;top:200px;font-size:31px;line-height:38px;color:#fff}
.strip{left:0;top:363px;width:821px;height:116px;background:var(--strip)}
.feature{top:381px;width:215px;display:flex;gap:12px}
.feature svg{flex:none}
.feature h3{font-size:14px;font-weight:400;color:#111;line-height:17px;margin-bottom:4px}
.feature p{font-size:8px;line-height:10px;color:#444}
.panel{left:62px;top:500px;width:691px;height:640px;background:#fff;border:1px solid var(--line)}
.heading{font-size:30px;color:#222;white-space:nowrap}
.lead{left:81px;top:561px;width:400px;font-size:12.5px;line-height:16px;color:#111}
.body{left:81px;top:601px;width:400px;font-size:9.5px;line-height:15px;color:var(--muted)}
.member{top:761px;width:103px;text-align:center}
.member .photo{height:70px;border:1px solid var(--line);background:linear-gradient(#dfe9f0,#9fb2c2)}
.member p{font-size:8.5px;line-height:11px;color:#222;margin-top:8px}
.member a{font-size:8px;color:var(--link);display:block;margin-top:5px;text-decoration:none}
.arrow{width:12px;height:12px;border-radius:50%;background:#cfcfcf}
.quote{left:83px;top:957px;width:394px;height:84px;background:var(--green);padding:18px 16px;font-style:italic;font-size:10.5px;line-height:14px;color:#1e2a00}
.cust-photo{left:84px;top:1060px;width:82px;height:63px;border:1px solid var(--line);background:linear-gradient(#e4e9ee,#3e5670)}
.cust-name{left:300px;top:1082px;width:147px;text-align:right;font-style:italic;font-size:10.5px;line-height:14px;color:#222}
.news{left:538px;width:200px;display:flex;gap:14px}
.date{flex:none;width:45px;height:60px;background:var(--blue);color:#fff;text-align:center;padding-top:4px;position:relative}
.date b{display:block;font-weight:300;font-size:25px;line-height:27px}
.date span{font-size:15px}
.date::after{content:"";position:absolute;right:-6px;top:8px;border:6px solid transparent;border-right:0;border-left-color:var(--blue)}
.news h4{font-size:10.5px;font-weight:400;line-height:13px;color:#111;margin-bottom:5px}
.news p{font-size:8.5px;line-height:11px;color:#444}
.help{left:538px;top:815px;width:197px;height:91px;border:1px solid var(--line);background:#fff}
.help-title{left:12px;top:12px;font-size:15px;line-height:18px;color:#111}
.help-photo{left:140px;top:0;width:56px;height:64px;background:linear-gradient(#f0d9c9,#c8a38c)}
.help-call{left:0;bottom:0;width:100%;height:26px;background:var(--green);color:#fff;font-size:15px;display:flex;align-items:center;justify-content:center}
.tags{left:544px;top:988px;width:120px;color:var(--blue-dark);line-height:18px}
.tags span{text-decoration:underline;margin-right:2px}
.footer{left:0;top:1140px;width:821px;height:60px;background:var(--blue);border-top:3px solid var(--blue-dark)}
.footer p{position:absolute;left:79px;font-size:8.5px;color:#fff}
.footer-brand{right:82px;top:20px;font-size:10px;font-weight:700;color:#fff}
</style>
</head>
<body>
<header class="abs header">
  <div class="abs brand"><span class="brand-dot"></span>VR ADVISORY</div>
  <div class="abs connect">Connect with us: <i></i><i></i></div>
  <div class="abs callline">Call: <span>0450 123 4567</span></div>
  <nav class="abs nav"><a>Home</a><a>Business Partner</a><a>References</a><a>Work with us</a><a>Contacts</a></nav>
</header>
<div class="abs rule"></div>

<section class="abs hero"></section>
<div class="abs hero-photo" role="img" aria-label="Close-up of a business handshake in blue tones"></div>
<h1 class="abs hero-title">VR ADVISORY</h1>
<p class="abs hero-sub cond">Get the Desired Information at the<br>Right Time and in the Correct Form.</p>

<section class="abs strip"></section>
<div class="abs feature" style="left:61px">
  <svg width="34" height="30" viewBox="0 0 34 30"><rect x="1" y="2" width="32" height="20" rx="2" fill="var(--blue)"/><rect x="4" y="5" width="26" height="14" fill="#5aa5d6"/><rect x="14" y="22" width="6" height="4" fill="var(--blue)"/><rect x="9" y="26" width="16" height="3" fill="var(--blue)"/></svg>
  <div><h3>Evolution support</h3><p>Do not let the problems curb your business. Evolution support was established with the aim to help our clients in all stages of the project...</p></div>
</div>
<div class="abs feature" style="left:300px">
  <svg width="32" height="30" viewBox="0 0 32 30"><path d="M2 24a14 14 0 1 1 28 0z" fill="var(--blue)"/><path d="M16 22l6-10" stroke="#fff" stroke-width="2.5"/><circle cx="16" cy="22" r="2.5" fill="#fff"/><circle cx="7" cy="19" r="1.5" fill="#fff"/><circle cx="10" cy="13" r="1.5" fill="#fff"/><circle cx="16" cy="11" r="1.5" fill="#fff"/></svg>
  <div><h3>Corporate Performance Management</h3><p>The information that drives your business. How many people in your company have the right information at the right time</p></div>
</div>
<div class="abs feature" style="left:548px">
  <svg width="30" height="30" viewBox="0 0 30 30"><circle cx="15" cy="15" r="14" fill="var(--blue)"/><path d="M15 15V1M15 15l12 7M15 15L3 22" stroke="#fff" stroke-width="2"/></svg>
  <div><h3>Business Intelligence</h3><p>Do not let the problems curb your business. Evolution support was established with the aim to help our clients in all stages of the project...</p></div>
</div>

<main class="abs panel"></main>
<h2 class="abs heading cond" style="left:80px;top:510px">WELCOME!</h2>
<p class="abs lead">How many people in your company have the desired information at the right time and in the correct form?</p>
<p class="abs body">For a company it is essential to exploit the wealth of information available to make them accessible to their managers in order to help them in choosing the right business strategies (see the trend of performance, generate estimates, assume future scenarios and future strategies of response.) VR Advisory helps you to manage this process as simple and fast!</p>

<h2 class="abs heading cond" style="left:80px;top:692px">OUR TEEM</h2>
<span class="abs arrow" style="left:88px;top:794px"></span>
<div class="abs member" style="left:107px"><div class="photo" role="img" aria-label="Portrait of a team member on the phone"></div><p>Sed faucibus vitae augue at faucibus.</p><a>Learn more &gt;&gt;</a></div>
<div class="abs member" style="left:235px"><div class="photo" role="img" aria-label="Portrait of a team member on the phone"></div><p>Sed faucibus vitae augue at faucibus.</p><a>Learn more &gt;&gt;</a></div>
<div class="abs member" style="left:361px"><div class="photo" role="img" aria-label="Portrait of a team member on the phone"></div><p>Sed faucibus vitae augue at faucibus.</p><a>Learn more &gt;&gt;</a></div>
<span class="abs arrow" style="left:470px;top:794px"></span>

<h2 class="abs heading cond" style="left:80px;top:904px">WHAT OUR CUSTOMERS SAY...</h2>
<blockquote class="abs quote">"Lorem ipsum dolor sit amet, consectetur adipiscing elit. Vivamus egestas fermentum tempor. Vivamus sit amet elit sit amet risus vehicula scelerisque. Donec blandit luctus massa, in scelerisque ex pellentesque et."</blockquote>
<svg class="abs" style="left:416px;top:1040px" width="32" height="14" viewBox="0 0 32 14"><path d="M0 0h32L16 14z" fill="var(--green)"/></svg>
<div class="abs cust-photo" role="img" aria-label="Portrait of a customer in a suit"></div>
<p class="abs cust-name">Customer name here<br><span style="font-size:9px">- Place here</span></p>

<h2 class="abs heading cond" style="left:534px;top:516px">RECENT NEWS</h2>
<div class="abs news" style="top:565px"><div class="date cond"><b>06</b><span>OCT</span></div><div><h4>LEDGER vince il Nimbusoft Corvex Swiss Inno...</h4><p>Lorem ipsum dolor sit amet, consectetur adipiscing elit.</p></div></div>
<div class="abs news" style="top:643px"><div class="date cond"><b>06</b><span>OCT</span></div><div><h4>LEDGER Spring Tour 2012</h4><p>Lorem ipsum dolor sit amet, consectetur adipiscing elit.</p></div></div>
<div class="abs news" style="top:720px"><div class="date cond"><b>06</b><span>OCT</span></div><div><h4>Nunc non bibendum nisl.</h4><p>Lorem ipsum dolor sit amet, consectetur adipiscing elit. Nullam condimentum libero quis est</p></div></div>

<aside class="abs help">
  <div class="abs help-photo" role="img" aria-label="Support operator wearing a headset"></div>
  <p class="abs help-title">Have any<br>Questions?</p>
  <div class="abs help-call">Call us: 0450 123 4567</div>
</aside>

<h2 class="abs heading cond" style="left:534px;top:938px">TAG CLOUD</h2>
<div class="abs tags">
  <span style="font-size:15px">analisi</span><span style="font-size:8px">utenti</span>
  <span style="font-size:13px">planning</span><span style="font-size:11px">nimbusoft</span>
  <span style="font-size:7px">software</span><span style="font-size:16px">dati</span><span style="font-size:6px">calendari</span>
  <span style="font-size:13px">report</span><span style="font-size:12px">business</span>
  <span style="font-size:9px">reports</span><span style="font-size:6px">datanote.example</span>
</div>

<footer class="abs footer">
  <p style="top:17px">VR Advisory S.r.l. - Via dei Tigli, 7 - 00000 Borgo Alto</p>
  <p style="top:32px">© Copyright VR Advisory 2014 All Rights Reserved.</p>
  <div class="abs footer-brand">VR ADVISORY</div>
</footer>
</body>
</html>
```